Change of trading name, rebrand

existing website to be updated with new theme and logo. existing website is
www.harlowbrentmere.com.au
Industry/Entity Type
Construction
Coding
Coded - Design and coding required
Number of Pages Required
5+ page
Requirements
Must have
- be mobile phone friendly

```html
<!DOCTYPE html>
<html lang="en">
<head>
<meta charset="utf-8">
<title>HBM Plant Hire</title>
<meta name="viewport" content="width=device-width, initial-scale=1">
<link href="https://fonts.googleapis.com/css2?family=Montserrat:wght@400;500;600;700;800;900&display=swap" rel="stylesheet">
<style>
:root{
  --navy:#23246f;
  --navy-dark:#1b1c5c;
  --ink:#222;
  --muted:#555;
  --footer:#1d1e2d;
  --line:#c9c9c9;
  --white:#fff;
}
*{box-sizing:border-box;margin:0;padding:0}
html,body{width:1200px;height:3975px;overflow:hidden}
body{font-family:"Montserrat",sans-serif;color:var(--ink);background:var(--white);position:relative}
a{color:inherit;text-decoration:none}
.abs{position:absolute}

.site-header{position:absolute;top:0;left:0;width:1200px;height:114px;background:var(--white)}
.header-phone{left:118px;top:38px;display:flex;align-items:center;gap:14px;font-size:15px}
.phone-badge{width:34px;height:28px;background:var(--navy);transform:skewX(-10deg);display:flex;align-items:center;justify-content:center;box-shadow:-4px 4px 0 -1px var(--white),-5px 5px 0 0 var(--navy)}
.brand{left:0;width:1200px;top:36px;text-align:center;font-weight:800;font-size:26px;color:var(--navy);letter-spacing:1px}
.brand small{display:block;font-size:10px;letter-spacing:3px;font-weight:800;margin-top:2px}
.btn{display:inline-block;background:var(--navy);color:var(--white);font-weight:700;font-size:13px;text-transform:uppercase;padding:12px 38px;transform:skewX(-12deg);box-shadow:-5px 5px 0 -2px var(--white),-6px 6px 0 -1px var(--navy)}
.btn span{display:inline-block;transform:skewX(12deg)}
.quote-btn{left:920px;top:31px;padding:12px 42px}
.main-nav{position:absolute;top:114px;left:0;width:1200px;height:43px;background:#1f1f24;display:flex;justify-content:center;align-items:center;gap:18px;color:#ddd;font-size:12px;font-weight:500}
.main-nav .active{color:var(--white);font-weight:700}
.main-nav .sep{color:#aaa}

.hero{position:absolute;top:157px;left:0;width:1200px;height:453px;background:linear-gradient(180deg,#9fb3cc 0%,#d6dde6 35%,#b4512a 55%,#4a4e73 75%,#2a2e72 100%)}
.hero-text{left:0;width:1200px;top:402px;text-align:center;color:var(--white)}
.hero-text .kicker{font-size:30px;font-weight:800}
.hero-text h1{font-size:56px;font-weight:900;line-height:1.1}
.hero-text .arrow{margin-top:10px}
.stripes{position:absolute;left:0;width:1200px}

.section-title{position:absolute;left:0;width:1200px;text-align:center;font-weight:900;font-size:44px;letter-spacing:.5px}
.section-title::after{content:"";display:block;width:46px;height:3px;background:var(--navy);margin:8px auto 0}
.about-sub{left:0;width:1200px;top:762px;text-align:center;font-size:19px;line-height:29px}
.about-sub b{font-weight:700}
.about-col{top:850px;width:470px;font-size:14px;line-height:25.7px;color:var(--muted)}
.features{left:111px;top:1285px;width:978px;display:flex;justify-content:space-between}
.feature{width:180px;text-align:center;font-size:14px;line-height:19px;font-weight:500}
.feature-icon{width:78px;height:78px;margin:0 auto 14px;border:2px solid var(--navy);padding:4px;background:var(--white)}
.feature-icon div{width:100%;height:100%;background:var(--navy);display:flex;align-items:center;justify-content:center}
.feature b{font-size:19px;font-weight:700;display:block;margin-bottom:2px}
.fleet-photo{left:0;top:1440px;width:1200px;height:303px;background:linear-gradient(180deg,#f6f6f8 0%,#c9a24a 45%,#b07a3a 75%,#a58257 100%)}

.plant{left:0;top:1743px;width:1200px;height:847px;background:var(--navy)}
.plant .section-title{color:var(--white);top:60px}
.plant .section-title::after{background:var(--white)}
.card{position:absolute;width:301px;height:235px;display:flex;align-items:flex-end;justify-content:center;padding-bottom:42px;color:var(--white);font-size:17px;font-weight:600;letter-spacing:.5px}
.view-btn{left:516px;top:2462px;background:#15162a;box-shadow:-5px 5px 0 -2px var(--navy),-6px 6px 0 -1px var(--white)}

.contact{left:0;top:2590px;width:1200px;height:572px;background:#f1f2f4}
.contact-sub{left:0;width:1200px;top:2730px;text-align:center;font-size:19px;line-height:29px}
.field{position:absolute;border:1px solid var(--line);background:var(--white);font-size:14px;padding:12px 21px;color:#333}
.submit-btn{left:521px;top:3064px}

.partners-row{position:absolute;left:0;width:1200px;display:flex;justify-content:center;gap:48px;align-items:center}
.badge{width:100px;height:46px;background:#e3e5ea;border-radius:4px}
.badge.tall{height:78px}

.footer{left:0;top:3578px;width:1200px;height:397px;background:var(--footer);color:#d8d8de}
.foot-col{position:absolute;top:108px;font-size:15px;line-height:26px}
.foot-col h4{font-size:18px;font-weight:600;color:var(--white);margin-bottom:14px}
.copyright{position:absolute;left:0;width:1200px;top:354px;text-align:center;font-size:14px}
</style>
</head>
<body>

<header class="site-header">
  <div class="abs header-phone">
    <span class="phone-badge"><svg width="14" height="14" viewBox="0 0 24 24"><path fill="#fff" d="M6.6 10.8a15 15 0 006.6 6.6l2.2-2.2a1 1 0 011-.25 11.4 11.4 0 003.6.6 1 1 0 011 1V20a1 1 0 01-1 1A17 17 0 013 4a1 1 0 011-1h3.5a1 1 0 011 1c0 1.250.2 2.45.6 3.6a1 1 0 01-.25 1z"/></svg></span>
    <span>1300 555 214</span>
  </div>
  <div class="abs brand">HBM<small>PLANT HIRE</small></div>
  <a class="abs btn quote-btn" href="#"><span>Get a Quote</span></a>
</header>

<nav class="main-nav">
  <a class="active" href="#">HOME</a><span class="sep">/</span>
  <a href="#">ABOUT US</a><span class="sep">/</span>
  <a href="#">PLANT HIRE</a><span class="sep">/</span>
  <a href="#">MAJOR PROJECT SNAPSHOT</a><span class="sep">/</span>
  <a href="#">POLICIES</a><span class="sep">/</span>
  <a href="#">JOBS</a><span class="sep">/</span>
  <a href="#">CONTACT US</a>
</nav>

<section class="hero" role="img" aria-label="Orange wheeled excavator parked in an equipment yard under a cloudy sky"></section>
<div class="abs hero-text">
  <div class="kicker">WELCOME TO</div>
  <h1>HBM PLANT HIRE</h1>
  <div class="arrow"><svg width="18" height="26" viewBox="0 0 18 26"><path d="M9 0v24M2 17l7 7 7-7" stroke="#fff" stroke-width="2" fill="none"/></svg></div>
</div>
<svg class="stripes" style="top:568px" width="1200" height="50" viewBox="0 0 1200 50">
  <polygon points="0,10 1200,40 1200,50 0,50" fill="#fff"/>
  <polygon points="0,12 1200,30 1200,34 0,20" fill="#fff"/>
  <polygon points="0,24 1200,40 1200,42 0,28" fill="#23246f"/>
</svg>

<h2 class="section-title" style="top:680px">ABOUT US</h2>
<p class="abs about-sub">HBM Heavy Equipment Hire<br><b>Committed to superior quality plant hire services.</b></p>
<p class="abs about-col" style="left:111px">Harlow Brentmere Heavy Equipment Hire specialise in the hire of heavy earthmoving, mining and construction machines with specialised attachments and tooling. Our array of machines and attachments is second to none, and we have one of the largest hire fleets available in South East Queensland. If its plant hire you require, then Harlow Brentmere Resources, or HBM as the local's call us – should be the first call you make. Wet or dry hire, we provide excellent operators and quality machines across all makes and models to guarantee you maximum up-time.</p>
<p class="abs about-col" style="left:621px">We employ a group of highly skilled and capable managers who have worked throughout construction sites in Queensland, NSW and other parts of Australia to deliver a vast array of plant and equipment to mining, civil, building and industrial projects. Our expertise is applied to every project to ensure delivery is achieved in accordance with project specifications, productivity and cost targets. We offer plant hire and civil construction services from Brisbane to the Surat Basin, Gold Coast, Sunshine Coast, Capricorn Coast, south to Ballina, Coffs Harbour, then through to Gladstone, Ipswich and Toowoomba. Harlow Brentmere Resources has Queensland covered!</p>
<a class="abs btn" style="left:624px;top:1170px;padding:12px 40px" href="#"><span>Learn More</span></a>

<div class="abs features">
  <div class="feature"><div class="feature-icon"><div><svg width="34" height="30" viewBox="0 0 34 30" fill="#fff"><path d="M17 2l2 4 4 .5-3 3 .8 4-3.8-2-3.8 2 .8-4-3-3 4-.5z"/><path d="M4 20h6l8 3 10-5 2 2-12 8H4z"/></svg></div></div><b>20+</b>Years of experience</div>
  <div class="feature"><div class="feature-icon"><div><svg width="36" height="26" viewBox="0 0 36 26" fill="#fff"><rect x="2" y="4" width="20" height="14"/><path d="M22 8h7l5 6v4H22z"/><circle cx="8" cy="21" r="3"/><circle cx="28" cy="21" r="3"/></svg></div></div><b>100+</b>Machines in fleet</div>
  <div class="feature"><div class="feature-icon"><div><svg width="26" height="32" viewBox="0 0 26 32" fill="#fff"><path d="M6 2l4 6 3-2 2 8 6 6 3 8H2l2-10-2-6z"/></svg></div></div>One of QLD's largest suppliers</div>
  <div class="feature"><div class="feature-icon"><div><svg width="32" height="32" viewBox="0 0 32 32" fill="#fff"><circle cx="12" cy="16" r="9"/><circle cx="12" cy="16" r="3.5" fill="#23246f"/><path d="M20 4l8 8-3 3-8-8zM22 18l6 10-3 2-6-10z"/></svg></div></div>Onsite servicing</div>
  <div class="feature"><div class="feature-icon"><div><svg width="30" height="32" viewBox="0 0 30 32" fill="#fff"><rect x="4" y="26" width="18" height="4"/><path d="M10 26l2-12h4l2 12z"/><circle cx="14" cy="10" r="4"/><path d="M16 8l8-4 2 3-8 4z"/></svg></div></div>Custom machine attachments</div>
</div>

<div class="abs fleet-photo" role="img" aria-label="Row of yellow graders and earthmoving machines lined up on a dirt yard"></div>

<section class="abs plant">
  <h2 class="section-title">PLANT HIRE</h2>
  <a class="card" style="left:111px;top:173px;background:linear-gradient(180deg,#a9bfd8,#7a6e62 60%,#a0714d)" role="img" aria-label="Loader beside stacked steel pipes">LOADER HIRE</a>
  <a class="card" style="left:449px;top:173px;background:linear-gradient(180deg,#5f7fa8,#4a4a40 55%,#6b5f3e)" role="img" aria-label="Yellow backhoe on site">BACKHOE HIRE</a>
  <a class="card" style="left:788px;top:173px;background:linear-gradient(180deg,#b4c1d0,#9b7e66 55%,#7d5d3c)" role="img" aria-label="Orange excavator digging a trench">EXCAVATOR HIRE</a>
  <a class="card" style="left:111px;top:439px;background:linear-gradient(180deg,#6f9bd6,#b08335 55%,#8b7453)" role="img" aria-label="Articulated dump truck">DUMP TRUCK HIRE</a>
  <a class="card" style="left:449px;top:439px;background:linear-gradient(180deg,#7a8a6a,#8f7a3a 55%,#6f6450)" role="img" aria-label="Skid steer bobcat">BOMBCAT HIRE</a>
  <a class="card" style="left:788px;top:439px;background:linear-gradient(180deg,#a9b0a3,#8d7a45 55%,#6e6a64)" role="img" aria-label="Padfoot compactor roller">COMPACTOR HIRE</a>
</section>
<a class="abs btn view-btn" href="#"><span>View All</span></a>
<svg class="stripes" style="top:2550px" width="1200" height="45" viewBox="0 0 1200 45">
  <polygon points="0,40 1200,5 1200,20 0,45" fill="#f1f2f4"/>
  <polygon points="300,30 1200,8 1200,14 300,33" fill="#15162a"/>
</svg>

<section class="abs contact" role="img" aria-label="Soft grey background with faint gear shapes"></section>
<h2 class="section-title" style="top:2650px">CONTACT US</h2>
<p class="abs contact-sub">Get in touch with us today for a<br><b>FREE QUOTE</b></p>
<div class="field" style="left:298px;top:2823px;width:296px;height:46px">Name</div>
<div class="field" style="left:606px;top:2823px;width:296px;height:46px">Phone</div>
<div class="field" style="left:298px;top:2883px;width:604px;height:45px">Email ID</div>
<div class="field" style="left:298px;top:2943px;width:604px;height:88px">Message</div>
<a class="abs btn submit-btn" href="#"><span>Submit Now</span></a>

<h2 class="section-title" style="top:3213px">TRUSTED PARTNERS</h2>
<div class="partners-row" style="top:3315px">
  <div class="badge"></div><div class="badge"></div><div class="badge"></div><div class="badge tall"></div><div class="badge"></div>
</div>
<div class="partners-row" style="top:3438px">
  <div class="badge"></div><div class="badge"></div><div class="badge"></div><div class="badge tall"></div><div class="badge"></div><div class="badge"></div>
</div>

<footer class="abs footer">
  <svg class="stripes" style="top:-2px" width="1200" height="40" viewBox="0 0 1200 40">
    <rect width="1200" height="40" fill="#fff"/>
    <polygon points="0,2 1000,2 0,24" fill="#23246f"/>
    <polygon points="0,28 1000,4 1000,8 0,32" fill="#1d1e2d"/>
    <polygon points="0,34 1200,14 1200,40 0,40" fill="#1d1e2d"/>
  </svg>
  <div class="foot-col" style="left:116px">
    <h4>Contact Us</h4>
    <p>&#9679;&nbsp; Head Office: 22 Kestrel Rd,<br>&nbsp;&nbsp;&nbsp;&nbsp;Brackenvale QLD 4291</p>
    <p style="margin-top:8px">&#9742;&nbsp; 1300 555 214</p>
  </div>
  <div class="foot-col" style="left:393px">
    <h4>Quick Links</h4>
    <p>Home<br>About us<br>Machine Operator Jobs<br>Plant Hire<br>Attachments Hire<br>Policies</p>
  </div>
  <div class="foot-col" style="left:662px">
    <h4>Other Links</h4>
    <p>Articulated Dump Trucks Hire<br>Dozer Hire<br>Excavator Diggers Hire<br>Grader Hire<br>Attachments Hire</p>
  </div>
  <div class="foot-col" style="left:958px">
    <h4>&nbsp;</h4>
    <p>Backhoe Hire<br>Compactors Hire<br>Loader Hire<br>Skid Steer Hire<br>Water Cart Hire</p>
  </div>
  <p class="copyright">2024 HBM. All Rights Reserved.</p>
</footer>

</body>
</html>
```